Adult Job Portal needs a Web Design

We need a web design for a landing and search page for an ADULT-JOB-portal.

The structure of landing page can be taken from tealpondmeetup.com.

The structure of job search page can be taken from: http://www.workroundvellmarsh.co.uk/

Users should be able to recognize that is a SEX-INDUSTRY job portal.

The project name can not be published for ... some reasons.
Updates

Hi, Plumvaners.

Please note: the project was upgraded to "Guaranteed"
Thanks in advance for great work.
BR. M.

Hi DesignPlumvaners,
please find attached the landing page wireframe.
It should make it easier for you to know what is expected.
Thanks in advance, guys!

Target Market(s)

women 18 to 30 years old

Industry/Entity Type

Adult

Requirements
Must have
• We expect to get design for the following pages:
- Landing page
- Add profile (name, description, photos, skills, preferable location)
- Job search with filters (example http://www.workroundvellmarsh.co.uk/jobs)
- Companies list (example http://www.workroundvellmarsh.co.uk/companies-in-oxfordshire)
- Company page (example http://www.workroundvellmarsh.co.uk/company/kolvuni)
Should not have
• pornography, violence

```html
<!DOCTYPE html>
<html lang="en">
<head>
<meta charset="utf-8">
<title>Velvet Hire — Jobs</title>
<link rel="stylesheet" href="https://fonts.googleapis.com/css2?family=Open+Sans:wght@400;600;700&display=swap">
<style>
  :root {
    --pink: #f0509a;
    --pink-deep: #e03d86;
    --pink-soft: #f778b2;
    --white: #ffffff;
    --ink-grey: #9a9a9a;
    --field-border: #cfcfcf;
    --tile-dark: rgba(20, 16, 16, 0.55);
    --tile-brown: rgba(70, 42, 30, 0.72);
    --tile-line: rgba(255, 255, 255, 0.28);
    --sky: #c9d6dc;
    --foliage: #5d7a4a;
    --skin: #d9a283;
    --skin-light: #eccbb4;
    --hair: #3a2620;
  }
  * { margin: 0; padding: 0; box-sizing: border-box; }
  html, body { width: 1200px; height: 851px; overflow: hidden; }
  body { font-family: "Open Sans", Arial, sans-serif; background: var(--white); }

  .page { position: relative; width: 1200px; height: 851px; overflow: hidden; }

  .hero-photo {
    position: absolute; inset: 0;
    background:
      radial-gradient(ellipse 260px 380px at 1000px 260px, rgba(58, 38, 32, 0.85), transparent 70%),
      radial-gradient(ellipse 330px 250px at 200px 500px, var(--skin) 0%, transparent 75%),
      radial-gradient(ellipse 320px 300px at 640px 560px, var(--skin) 0%, transparent 75%),
      radial-gradient(ellipse 300px 260px at 150px 160px, var(--foliage) 0%, transparent 75%),
      linear-gradient(100deg, #8e9b86 0%, var(--sky) 38%, var(--skin-light) 70%, #cbb9a6 100%);
  }

  /* Brand */
  .brand { position: absolute; left: 96px; top: 37px; width: 290px; height: 160px; }
  .brand svg { position: absolute; inset: 0; }
  .brand-name {
    position: absolute; left: 0; right: 0; top: 58px;
    text-align: center; color: var(--pink);
    font-size: 34px; font-weight: 600; letter-spacing: 0.5px;
  }

  /* Social */
  .social { position: absolute; top: 28px; left: 944px; display: flex; gap: 22px; }
  .social-dot { width: 28px; height: 28px; border-radius: 50%; background: rgba(255,255,255,0.85); }
  .social-dot.is-active { background: var(--pink); }
  .tooltip {
    position: absolute; left: 871px; top: 63px; width: 175px; height: 37px;
    background: var(--white); border-radius: 3px;
    color: var(--ink-grey); font-size: 10.5px; line-height: 37px; text-align: center;
  }

  /* Account box */
  .account { position: absolute; left: 549px; top: 100px; width: 193px; }
  .account-btn {
    display: block; margin: 0 auto; width: 153px; height: 40px;
    background: var(--pink); color: var(--white);
    font-size: 13px; text-align: center; line-height: 44px; border-radius: 6px 6px 0 0;
  }
  .account-btn.signup { border-radius: 0 0 6px 6px; line-height: 38px; position: relative; }
  .account-btn.signup::after {
    content: ""; position: absolute; left: 68px; bottom: -10px;
    border: 6px solid transparent; border-top: 6px solid var(--pink); border-bottom: 0;
    border-left-width: 7px; border-right-width: 7px;
  }
  .jobs-count {
    height: 48px; background: var(--white); border-radius: 7px;
    color: var(--pink); font-size: 14px; text-align: center; line-height: 48px;
  }

  /* Search */
  .search-field {
    position: absolute; top: 244px; height: 30px; width: 297px;
    background: var(--white); border: 1px solid var(--field-border);
    color: #b5b5b5; font-size: 10px; line-height: 28px; padding-left: 11px;
  }
  .search-field .clear {
    position: absolute; right: 8px; top: 0; color: #555; font-size: 13px; font-weight: 700;
  }
  .search-what { left: 228px; }
  .search-where { left: 547px; }
  .search-btn {
    position: absolute; left: 866px; top: 244px; width: 183px; height: 30px;
    background: linear-gradient(var(--pink-soft), var(--pink-deep));
    border-radius: 4px 10px 4px 10px;
    color: var(--white); font-size: 11px; font-weight: 600; text-align: center; line-height: 30px;
  }

  /* Slider arrows */
  .slide-arrow { position: absolute; top: 378px; }
  .slide-arrow.prev { left: 34px; }
  .slide-arrow.next { left: 1142px; }

  /* Navigation tiles */
  .nav-tile {
    position: absolute; top: 406px; width: 186px; height: 92px;
    background: var(--tile-dark); border: 1px solid var(--tile-line);
    padding: 30px 0 0 26px; color: var(--white);
  }
  .nav-title { font-size: 18px; line-height: 20px; }
  .nav-sub { color: var(--pink); font-size: 8.5px; font-weight: 600; margin-left: 1px; }
  .tile-home { left: 132px; }
  .tile-about { left: 320px; }
  .tile-blog { left: 696px; background: var(--tile-brown); }
  .tile-contact { left: 884px; }
  .tile-photo {
    position: absolute; left: 508px; top: 371px; width: 187px; height: 128px;
    border: 1px solid var(--tile-line);
    background: linear-gradient(180deg, #8b8da7 0%, #c7aaa0 55%, #eee 100%);
  }
  .tile-services {
    position: absolute; left: 509px; top: 498px; width: 186px; height: 129px;
    background: var(--tile-brown); border: 1px solid var(--tile-line);
    padding: 48px 0 0 22px; color: var(--white);
  }
  .services-menu {
    position: absolute; left: 695px; top: 498px; width: 186px; height: 128px;
    background: rgba(28, 22, 22, 0.72); list-style: none; padding: 18px 0 0 19px;
  }
  .services-menu li { color: var(--pink); font-size: 9.5px; font-weight: 600; height: 19.8px; }
  .services-menu li.is-current { color: var(--white); }

  /* Pager */
  .pager { position: absolute; top: 762px; left: 511px; display: flex; gap: 7px; }
  .pager span { width: 18px; height: 18px; border: 2px solid var(--white); border-radius: 50%; }
  .pager span.is-active { background: var(--pink); }

  .footer {
    position: absolute; top: 825px; left: 0; width: 1170px; text-align: center;
    color: var(--white); font-size: 8.5px; font-weight: 600;
  }
  .footer a { color: var(--pink); text-decoration: none; }
</style>
</head>
<body>
<div class="page">
  <div class="hero-photo" role="img" aria-label="Full-bleed lifestyle photograph of a smiling dark-haired woman in swimwear lounging poolside"></div>

  <div class="brand">
    <svg width="290" height="160" viewBox="0 0 290 160">
      <path d="M145 4 C160 18 180 22 200 26 C260 30 288 50 288 82 C288 114 262 126 210 132 C185 135 165 142 145 157 C125 142 105 135 80 132 C28 126 2 114 2 82 C2 50 30 30 90 26 C110 22 130 18 145 4 Z"
            fill="#ffffff" stroke="#e0519a" stroke-width="3"/>
    </svg>
    <div class="brand-name">Velvet Hire</div>
  </div>

  <div class="social">
    <span class="social-dot is-active"></span>
    <span class="social-dot"></span>
    <span class="social-dot"></span>
    <span class="social-dot"></span>
  </div>
  <div class="tooltip">BECOME A FAN ON CHATTERBOOK</div>

  <div class="account">
    <a class="account-btn">LOGIN</a>
    <div class="jobs-count">1000 JOBS AVAILABLE</div>
    <a class="account-btn signup">SIGN UP!</a>
  </div>

  <div class="search-field search-what">WHAT ARE YOU LOOKING FOR?<span class="clear">×</span></div>
  <div class="search-field search-where">WHERE IN NEWYORK?<span class="clear">×</span></div>
  <div class="search-btn">FIND JOBS</div>

  <svg class="slide-arrow prev" width="24" height="90" viewBox="0 0 24 90"><path d="M20 2 L3 45 L20 88" fill="none" stroke="#ffffff" stroke-width="3"/></svg>
  <svg class="slide-arrow next" width="24" height="90" viewBox="0 0 24 90"><path d="M4 2 L21 45 L4 88" fill="none" stroke="#ffffff" stroke-width="3"/></svg>

  <div class="nav-tile tile-home"><div class="nav-title">HOME</div><div class="nav-sub">LOREM IPSUM</div></div>
  <div class="nav-tile tile-about"><div class="nav-title">ABOUT US</div><div class="nav-sub">GET TO KNOW ME</div></div>
  <div class="tile-photo" role="img" aria-label="Portrait photograph of a woman resting on a pillow"></div>
  <div class="nav-tile tile-blog"><div class="nav-title">BLOG</div><div class="nav-sub">I WRITE ABOUT SEX SERVICE</div></div>
  <div class="nav-tile tile-contact"><div class="nav-title">CONTACT US</div><div class="nav-sub">HOW TO FIND US</div></div>

  <div class="tile-services"><div class="nav-title">SERVICES</div><div class="nav-sub">WHAT WE DO!</div></div>
  <ul class="services-menu">
    <li>SERVICE 1</li>
    <li>SERVICE 2</li>
    <li class="is-current">SERVICE 3</li>
    <li>SERVICE 4</li>
    <li>SERVICE 5</li>
  </ul>

  <div class="pager"><span class="is-active"></span><span></span><span></span><span></span><span></span></div>

  <div class="footer">© COPYRIGHTS 2013.VELVET HIRE . <a>PRIVACY POLICY</a></div>
</div>
</body>
</html>
```